Cedarvale Ridge College

We are looking to update our current webpage at www.cedarvaleridge.ca. We would like to make it modern, fresh and appealing to students. We want to keep our logo the same with the logo colours blended in as the primary colours and focus. We are open to reconfiguring content as well.
Reason: Hi, In the next 3 days we will have narrowed our search to 3 designs and will make a choice before the final deadline...
College

```html
<!DOCTYPE html>
<html lang="en">
<head>
<meta charset="utf-8">
<title>Cedarvale Ridge College</title>
<link rel="stylesheet" href="https://fonts.googleapis.com/css2?family=Mulish:wght@400;600;700&family=Kalam:wght@400;700&display=swap">
<style>
:root{
  --navy:#1f3272;
  --navy-dark:#17285e;
  --teal:#0a5c55;
  --teal-dark:#0b4d46;
  --teal-bright:#13a898;
  --footer:#075a52;
  --text:#5a5a5a;
  --rule:#dcdcdc;
  --card:#f5f5f5;
  --white:#ffffff;
}
*{box-sizing:border-box;margin:0;padding:0}
html,body{width:1133px;height:1200px;overflow:hidden;background:var(--white);font-family:"Mulish",sans-serif;color:var(--text)}
.page{position:relative;width:1133px;height:1200px}
.top-rule{position:absolute;left:0;top:0;width:100%;height:3px;background:var(--teal)}
.utility{position:absolute;left:767px;top:0;width:296px;height:35px;background:var(--teal);display:flex;align-items:center;justify-content:center;gap:10px;font-size:11px;color:var(--white);white-space:nowrap}
.utility span.sep{opacity:.7}
.brand{position:absolute;left:71px;top:44px;display:flex;align-items:center;gap:8px;font-size:17px;font-weight:700;color:var(--navy);line-height:1.05;width:170px}
.brand .mark{width:14px;height:14px;border-radius:50%;background:var(--navy);flex:none}
.tagline{position:absolute;left:261px;top:46px;display:flex;align-items:center;gap:26px;font-family:"Kalam",cursive;font-size:27px;color:#8c8c8c}
.tagline svg{width:12px;height:16px}
.connect{position:absolute;left:858px;top:56px;display:flex;align-items:center;gap:6px;font-size:12px;color:var(--navy-dark);font-weight:600;white-space:nowrap}
.connect .social{width:28px;height:28px;border-radius:50%}
.s1{background:#3b5a9a}.s2{background:#2aa3e3}.s3{background:#f28c1c}.s4{background:#e0322a}
.nav{position:absolute;left:70px;top:95px;width:993px;height:41px;background:linear-gradient(#233a7c,var(--navy-dark));display:flex;font-size:10.5px;color:var(--white)}
.nav a{flex:1 1 auto;display:flex;align-items:center;justify-content:center;padding:0 6px;color:inherit;text-decoration:none;white-space:nowrap}
.nav a.active{background:var(--teal);flex:0 0 auto;padding:0 14px}
.hero{position:absolute;left:70px;top:141px;width:993px;height:355px;overflow:hidden;background:#0c6e63}
.hero .photo{position:absolute;left:330px;top:0;width:663px;height:355px;background:linear-gradient(90deg,#0e7466 0%,#6b8f9a 30%,#8aa0b8 55%,#4d6fa3 75%,#9ab0c5 100%)}
.hero .fade{position:absolute;left:0;top:0;width:560px;height:355px;background:linear-gradient(90deg,#0b6b62 0%,#0e7467 55%,rgba(14,116,103,0) 100%)}
.hero h1{position:absolute;left:45px;top:44px;font-family:"Kalam",cursive;font-weight:700;font-size:80px;color:var(--white);line-height:1}
.hero p{position:absolute;left:45px;top:143px;width:360px;font-size:16px;line-height:22px;color:var(--white);font-weight:600}
.hero .cta{position:absolute;left:45px;top:223px;width:124px;height:35px;background:var(--teal-bright);color:var(--white);font-size:16px;font-weight:600;display:flex;align-items:center;justify-content:center}
.dots{position:absolute;left:45px;top:316px;display:flex;gap:6px}
.dots i{width:11px;height:11px;border-radius:50%;background:rgba(255,255,255,.35)}
.dots i.on{background:var(--white)}
.hero-shadow{position:absolute;left:90px;top:496px;width:953px;height:26px;background:radial-gradient(ellipse at top,rgba(0,0,0,.28),rgba(0,0,0,0) 70%)}
h2{font-weight:400;font-size:21px;color:var(--navy);letter-spacing:.2px;white-space:nowrap}
.welcome h2{position:absolute;left:70px;top:542px}
.welcome .img{position:absolute;left:70px;top:583px;width:196px;height:139px;background:linear-gradient(90deg,#8c8f7d,#d9d7cf 50%,#9aa08e)}
.welcome p{position:absolute;left:283px;top:580px;width:515px;font-size:11px;line-height:20px}
.btn-dark{position:absolute;left:283px;top:694px;width:87px;height:28px;background:var(--teal-dark);color:var(--white);font-size:11px;display:flex;align-items:center;justify-content:center}
.vrule{position:absolute;left:809px;top:547px;width:1px;height:174px;background:var(--rule)}
.admission h2{position:absolute;left:835px;top:542px}
.admission ul{position:absolute;left:835px;top:581px;list-style:none;font-size:12px;line-height:21px;white-space:nowrap}
.admission li{display:flex;align-items:center;gap:11px}
.admission li::before{content:"";width:6px;height:6px;border-radius:50%;background:var(--teal)}
.hrule{position:absolute;left:70px;top:752px;width:993px;height:1px;background:var(--rule)}
.card{position:absolute;top:777px;width:311px;height:288px;background:var(--card);border:1px solid #e6e6e6}
.card::after{content:"";position:absolute;left:15px;right:15px;bottom:-16px;height:16px;background:radial-gradient(ellipse at top,rgba(0,0,0,.22),rgba(0,0,0,0) 70%)}
.card h2{position:absolute;left:20px;top:13px}
.card .arrows{position:absolute;right:20px;top:20px;display:flex;gap:14px}
.card .media{position:absolute;left:20px;top:50px;width:270px;height:117px}
.card h3{position:absolute;left:20px;top:181px;font-size:16.5px;font-weight:600;color:var(--teal)}
.card p{position:absolute;left:20px;top:206px;width:270px;font-size:11.5px;line-height:17.5px}
.card .more{position:absolute;left:20px;font-size:11.5px;color:var(--navy);font-weight:600}
.c1{left:70px}.c2{left:411px}.c3{left:751px}
.m1{background:linear-gradient(90deg,#e4e2dc,#d8d3c8 60%,#2e3c58)}
.m2{background:linear-gradient(180deg,#2f3f58,#5d6b5a 55%,#3f5a3a)}
.m3{background:linear-gradient(180deg,#c9c7c0,#3b3a3a 60%,#6e5a4a)}
.play{position:absolute;left:50%;top:50%;transform:translate(-50%,-50%)}
.footer{position:absolute;left:0;top:1098px;width:1133px;height:102px;background:var(--footer)}
.footer nav{position:absolute;top:20px;left:0;width:100%;display:flex;justify-content:center;gap:23px;font-size:10px;color:var(--white);white-space:nowrap}
.footer .copy{position:absolute;top:53px;width:100%;text-align:center;font-size:10.5px;line-height:16px;color:var(--teal-bright)}
</style>
</head>
<body>
<div class="page">
  <div class="top-rule"></div>
  <div class="utility"><span>Apply Today</span><span class="sep">|</span><span>Donate</span><span class="sep">|</span><span>Library</span><span class="sep">|</span><span>Text for Info</span></div>

  <div class="brand"><span class="mark"></span><span>Cedarvale Ridge College</span></div>

  <div class="tagline">
    <span>Educate</span>
    <svg viewBox="0 0 12 16"><path d="M2 1l8 7-8 7" fill="none" stroke="#b5b5b5" stroke-width="3"/></svg>
    <span>Equip</span>
    <svg viewBox="0 0 12 16"><path d="M2 1l8 7-8 7" fill="none" stroke="#b5b5b5" stroke-width="3"/></svg>
    <span>Enrich</span>
  </div>

  <div class="connect"><span>Connect Us:</span>
    <span class="social s1"></span><span class="social s2"></span><span class="social s3"></span><span class="social s4"></span>
  </div>

  <nav class="nav">
    <a class="active">HOME</a><a>ABOUT US</a><a>CONSIDER CEDARVALE</a><a>CURRENT STUDENT</a><a>CURRENT STUDENTS</a><a>ALUMNI</a><a>SUPPORTERS</a><a>NEWS &amp; EVENTS</a><a>CEDARVALE PARK</a><a>CONTACT US</a>
  </nav>

  <section class="hero">
    <div class="photo" role="img" aria-label="Group of smiling students studying together with a laptop and book"></div>
    <div class="fade"></div>
    <h1>Educate</h1>
    <p>Aliquam molestie, mi et imperdiet euismod, dui purus auctor tellus, et interdum lacus lectus et ante.</p>
    <div class="cta">Apply Today</div>
    <div class="dots"><i class="on"></i><i></i><i></i><i></i></div>
  </section>
  <div class="hero-shadow"></div>

  <section class="welcome">
    <h2>WELCOME TO CEDARVALE RIDGE COLLEGE</h2>
    <div class="img" role="img" aria-label="Group photo of students in matching shirts"></div>
    <p>Aliquam molestie, mi et imperdiet euismod, dui purus auctor tellus, et interdum lacus lectus et ante. Sed accumsan sollicitudin sapien, sit amet adipiscing turpis gravida ac. In congue, neque ac lobortis volutpat, libero mauris varius mi, vitae suscipit ipsum ligula vitae risus. Duis aliquam nibh a dui iaculis viverra id a velit. Vivamus egestas risus in magna varius commodo. Sed semper viverra egestas. Etiam pretium porttitor lectus, vel ornare neque porta volutpat.</p>
    <div class="btn-dark">READ MORE</div>
  </section>
  <div class="vrule"></div>

  <section class="admission">
    <h2>ADMISSION</h2>
    <ul>
      <li>Download the full Catalogue</li>
      <li>Apply Today (Application Package)</li>
      <li>Information Request</li>
      <li>Browse our Programs</li>
      <li>Download Forms</li>
      <li>Admissions Information</li>
      <li>Campus Directory</li>
    </ul>
  </section>

  <div class="hrule"></div>

  <article class="card c1">
    <h2>NEWS &amp; EVENTS</h2>
    <div class="arrows"><svg width="10" height="16" viewBox="0 0 10 16"><path d="M8 1L2 8l6 7" fill="none" stroke="#1f3272" stroke-width="2"/></svg><svg width="10" height="16" viewBox="0 0 10 16"><path d="M2 1l6 7-6 7" fill="none" stroke="#1f3272" stroke-width="2"/></svg></div>
    <div class="media m1" role="img" aria-label="Instructor pointing at sheet music on a whiteboard"></div>
    <h3>Sound Production and Media</h3>
    <p>Cedarvale Ridge College is pleased to offer a one year program that is geared towards equipping a music student...</p>
    <span class="more" style="top:269px">Read More ››</span>
  </article>

  <article class="card c2">
    <h2>CEDARVALE VIDEOS</h2>
    <div class="arrows"><svg width="10" height="16" viewBox="0 0 10 16"><path d="M8 1L2 8l6 7" fill="none" stroke="#1f3272" stroke-width="2"/></svg><svg width="10" height="16" viewBox="0 0 10 16"><path d="M2 1l6 7-6 7" fill="none" stroke="#1f3272" stroke-width="2"/></svg></div>
    <div class="media m2" role="img" aria-label="Campus entrance sign video still">
      <svg class="play" width="48" height="48" viewBox="0 0 48 48"><circle cx="24" cy="24" r="22" fill="none" stroke="#fff" stroke-width="3"/><path d="M19 14l14 10-14 10z" fill="#fff"/></svg>
    </div>
    <h3>The Future is Bright</h3>
    <p>Visit Cedarvale's video channel for more videos...</p>
    <span class="more" style="top:259px">Read More ››</span>
  </article>

  <article class="card c3">
    <h2>OUR CAMPUS</h2>
    <div class="arrows"><svg width="10" height="16" viewBox="0 0 10 16"><path d="M8 1L2 8l6 7" fill="none" stroke="#1f3272" stroke-width="2"/></svg><svg width="10" height="16" viewBox="0 0 10 16"><path d="M2 1l6 7-6 7" fill="none" stroke="#1f3272" stroke-width="2"/></svg></div>
    <div class="media m3" role="img" aria-label="Students gathered in a classroom"></div>
    <h3>Photo Tour</h3>
    <p>Cedarvale Ridge College is pleased to offer a one year program that is geared towards equipping a music student...</p>
    <span class="more" style="top:269px">Read More ››</span>
  </article>

  <footer class="footer">
    <nav><span>HOME</span><span>ABOUT US</span><span>CONSIDER CEDARVALE</span><span>CURRENT STUDENT</span><span>CURRENT STUDENTS</span><span>ALUMNI</span><span>SUPPORTERS</span><span>NEWS &amp; EVENTS</span><span>CEDARVALE PARK</span><span>CONTACT US</span></nav>
    <div class="copy">Copyright © 2014. Cedarvale Ridge College.<br>All Right Reserved</div>
  </footer>
</div>
</body>
</html>
```